Copper Lantern

Need a business card for our restaurant. Restaurant and Bar in the mountains of North Idaho. Rustic looking card

rustic design, wood and metal looking, primarily neutral colors

• Name, address, phone number, website, email address

```html
<!DOCTYPE html>
<html lang="en">
<head>
<meta charset="utf-8">
<title>Copper Lantern – Business Card</title>
<link rel="stylesheet" href="https://fonts.googleapis.com/css2?family=Roboto:wght@400;500;700&display=swap">
<style>
  :root {
    --page-bg: #d6cdc0;
    --card-top: #efe8dc;
    --card-bottom: #e2d7c6;
    --card-edge: #b08a62;
    --card-edge-inner: #f6f1e8;
    --ink: #161412;
    --ink-soft: #2b2724;
    --icon-cut: #ebe3d6;
  }
  * { margin: 0; padding: 0; box-sizing: border-box; }
  html, body {
    width: 1047px;
    height: 1200px;
    overflow: hidden;
    background: var(--page-bg);
    font-family: "Roboto", Arial, sans-serif;
    color: var(--ink);
  }
  .canvas {
    width: 1047px;
    height: 1200px;
    display: flex;
    align-items: center;
    justify-content: center;
  }
  .card {
    width: 520px;
    height: 950px;
    background: linear-gradient(172deg, var(--card-top) 0%, var(--card-bottom) 100%);
    border: 2px solid var(--card-edge);
    box-shadow: inset 0 0 0 4px var(--card-edge-inner);
    border-radius: 26px;
    display: flex;
    flex-direction: column;
    align-items: center;
  }
  .brand {
    margin-top: 90px;
    height: 250px;
    display: flex;
    align-items: center;
    gap: 16px;
  }
  .brand-dot {
    width: 30px;
    height: 30px;
    border-radius: 50%;
    background: var(--ink);
  }
  .brand-name {
    font-size: 42px;
    font-weight: 500;
    letter-spacing: 1px;
    color: var(--ink);
  }
  .person {
    margin-top: 140px;
    text-align: center;
  }
  .person-name {
    font-size: 40px;
    font-weight: 700;
    letter-spacing: -0.5px;
    line-height: 48px;
  }
  .person-title {
    margin-top: 4px;
    font-size: 24px;
    font-weight: 400;
    color: var(--ink-soft);
  }
  .divider {
    display: block;
    width: 520px;
    height: 41px;
    margin-top: 16px;
  }
  .contact {
    margin-top: 10px;
    text-align: center;
    font-size: 24px;
    font-style: normal;
    line-height: 35px;
    color: var(--ink-soft);
  }
  .divider.pin-row { margin-top: 8px; }
</style>
</head>
<body>
<main class="canvas">
  <article class="card">
    <header class="brand">
      <span class="brand-dot"></span>
      <span class="brand-name">Copper Lantern</span>
    </header>

    <section class="person">
      <h1 class="person-name">Owen Hartley</h1>
      <p class="person-title">Managing Director</p>
    </section>

    <svg class="divider" viewBox="0 0 560 44" aria-hidden="true">
      <g fill="var(--ink)">
        <circle cx="22" cy="22" r="4"/><circle cx="44" cy="22" r="5"/>
        <circle cx="68" cy="22" r="6"/><circle cx="95" cy="22" r="7.5"/>
        <circle cx="125" cy="22" r="9"/><circle cx="158" cy="22" r="10.5"/>
        <circle cx="538" cy="22" r="4"/><circle cx="516" cy="22" r="5"/>
        <circle cx="492" cy="22" r="6"/><circle cx="465" cy="22" r="7.5"/>
        <circle cx="435" cy="22" r="9"/><circle cx="402" cy="22" r="10.5"/>
        <circle cx="214" cy="22" r="19"/>
        <circle cx="280" cy="22" r="19"/>
        <circle cx="346" cy="22" r="19"/>
      </g>
      <g fill="none" stroke="var(--icon-cut)" stroke-width="2.2" stroke-linecap="round" stroke-linejoin="round">
        <path d="M206 13 c-2 2 -2 6 1 11 c3 5 7 8 10 9 c2 0 4 -1 5 -3 l-4 -4 l-3 2 c-2 -1 -5 -4 -6 -7 l2 -3 z"/>
        <path d="M218 14 a6 6 0 0 1 6 6 M218 10 a10 10 0 0 1 10 10"/>
        <rect x="270" y="15" width="20" height="14" rx="2"/>
        <path d="M270 16 l10 7 l10 -7"/>
        <circle cx="346" cy="22" r="10"/>
        <path d="M336 22 h20 M346 12 c-5 6 -5 14 0 20 M346 12 c5 6 5 14 0 20"/>
      </g>
    </svg>

    <address class="contact">
      123 456 789<br>
      info@yourgmail.com<br>
      www.yourwebsite.com
    </address>

    <svg class="divider pin-row" viewBox="0 0 560 44" aria-hidden="true">
      <g fill="var(--ink)">
        <circle cx="22" cy="22" r="4"/><circle cx="46" cy="22" r="5"/>
        <circle cx="72" cy="22" r="6.5"/><circle cx="100" cy="22" r="8"/>
        <circle cx="130" cy="22" r="9"/><circle cx="162" cy="22" r="10.5"/>
        <circle cx="197" cy="22" r="11.5"/><circle cx="233" cy="22" r="12.5"/>
        <circle cx="538" cy="22" r="4"/><circle cx="514" cy="22" r="5"/>
        <circle cx="488" cy="22" r="6.5"/><circle cx="460" cy="22" r="8"/>
        <circle cx="430" cy="22" r="9"/><circle cx="398" cy="22" r="10.5"/>
        <circle cx="363" cy="22" r="11.5"/><circle cx="327" cy="22" r="12.5"/>
        <circle cx="280" cy="22" r="19"/>
      </g>
      <path d="M280 33 c-5 -6 -8 -10 -8 -14 a8 8 0 0 1 16 0 c0 4 -3 8 -8 14 z" fill="none" stroke="var(--icon-cut)" stroke-width="2.2" stroke-linejoin="round"/>
      <circle cx="280" cy="19" r="2.8" fill="var(--icon-cut)"/>
    </svg>

    <address class="contact">
      Your address, City<br>
      State, Zip 1234
    </address>
  </article>
</main>
</body>
</html>
```